Indy Film Production Company/Studio

We need a business card designed from an existing logo. We are a digital studio/production company that caters to creating genre entertainment, like Action, Horror, and martial arts. The card along with the logo will be used to Brand the company from letter heads to banners. The design will also be used for postcards and Brochures. It should be professional and masculine.
Updates

Thank you to all the designers who have participated. I'm narrowing down who it will be. Thank you again.

Target Market(s)

Investors, Networks, Producers, and actors

Industry/Entity Type

Film Production

Contact Information for Business Card

Teodoro Valbuena
Producer/Writer/Director
www.kestrelpicturehouse.example

Requirements
Must have
• Website address, Facebook icon and Twitter icon possibly in the back of the card.
Nice to have
• Logline of Company: Follow The Action.

```html
<!DOCTYPE html>
<html lang="en">
<head>
<meta charset="utf-8">
<title>Kestrel Picture House — Business Card</title>
<link href="https://fonts.googleapis.com/css2?family=Open+Sans:wght@400;600;800&display=swap" rel="stylesheet">
<style>
  :root {
    --backdrop: #3a3533;
    --card: #0c0c0c;
    --brand-red: #e3201f;
    --ink-light: #f2f2f2;
    --rule: #4a4a4a;
    --card-w: 520px;
    --card-h: 297px;
  }
  * { box-sizing: border-box; margin: 0; padding: 0; }
  html, body {
    width: 1200px; height: 814px; overflow: hidden;
    background: var(--backdrop);
    font-family: "Open Sans", Arial, sans-serif;
  }
  .canvas {
    position: relative; width: 1200px; height: 814px;
    display: flex; align-items: center; justify-content: center; gap: 60px;
  }
  .card {
    position: relative;
    width: var(--card-w); height: var(--card-h);
    background: var(--card);
    box-shadow: 0 12px 30px rgba(0,0,0,.45);
  }

  /* Front: contact side */
  .card--front { display: flex; align-items: center; padding: 0 36px; }
  .brand-block {
    width: 210px;
    color: var(--brand-red);
    font-weight: 800;
    text-transform: uppercase;
    line-height: 1.02;
  }
  .brand-block .brand-line { display: block; font-size: 30px; letter-spacing: .5px; }
  .brand-block .brand-line--small { font-size: 16px; letter-spacing: 2.4px; margin-top: 4px; }
  .divider {
    width: 1px; height: 150px; background: var(--rule); margin: 0 26px 0 14px;
  }
  .contact-name { color: var(--brand-red); font-size: 17px; font-weight: 600; }
  .contact-role { color: var(--ink-light); font-size: 12.5px; margin-bottom: 14px; }
  .contact-list { list-style: none; }
  .contact-list li {
    display: flex; align-items: center; gap: 8px;
    color: var(--ink-light); font-size: 11.5px; margin-bottom: 6px;
  }
  .contact-list svg { width: 12px; height: 12px; flex: none; }

  /* Back: brand side */
  .card--back {
    display: flex; flex-direction: column; align-items: center; justify-content: center;
  }
  .social-mark {
    position: absolute; top: 14px; right: 16px;
    width: 18px; height: 18px; background: var(--brand-red);
  }
  .back-brand {
    color: var(--brand-red); font-weight: 800; text-transform: uppercase;
    text-align: center; line-height: 1.02;
  }
  .back-brand .brand-line { display: block; font-size: 44px; letter-spacing: 1px; }
  .back-brand .brand-line--small { font-size: 20px; letter-spacing: 3.6px; margin-top: 6px; }
  .back-url {
    color: var(--ink-light); font-size: 12px; letter-spacing: .8px; margin-top: 20px;
  }
</style>
</head>
<body>
<main class="canvas">

  <section class="card card--front" aria-label="Business card front">
    <div class="brand-block">
      <span class="brand-line">Kestrel</span>
      <span class="brand-line brand-line--small">Picture House</span>
    </div>
    <div class="divider"></div>
    <div class="contact">
      <p class="contact-name">Teodoro Valbuena</p>
      <p class="contact-role">Producer/Writer/Director</p>
      <ul class="contact-list">
        <li>
          <svg viewBox="0 0 12 12" aria-hidden="true"><path fill="#e3201f" d="M2.5 1 L4.5 1 L5.2 3.6 L4 4.6 C4.7 6 6 7.3 7.4 8 L8.4 6.8 L11 7.5 L11 9.5 C11 10.3 10.3 11 9.5 11 C5 11 1 7 1 2.5 C1 1.7 1.7 1 2.5 1 Z"/></svg>
          555 014 2290
        </li>
        <li>
          <svg viewBox="0 0 12 12" aria-hidden="true"><rect x="1" y="2.5" width="10" height="7" fill="#e3201f"/><path d="M1 2.5 L6 6.5 L11 2.5" fill="none" stroke="#0c0c0c" stroke-width="1"/></svg>
          hello@kestrelpicturehouse.example
        </li>
        <li>
          <svg viewBox="0 0 12 12" aria-hidden="true"><circle cx="6" cy="6" r="5" fill="#e3201f"/><path d="M1 6 H11 M6 1 C3.5 3.5 3.5 8.5 6 11 M6 1 C8.5 3.5 8.5 8.5 6 11" fill="none" stroke="#0c0c0c" stroke-width=".8"/></svg>
          www.kestrelpicturehouse.example
        </li>
      </ul>
    </div>
  </section>

  <section class="card card--back" aria-label="Business card back">
    <span class="social-mark" aria-hidden="true"></span>
    <div class="back-brand">
      <span class="brand-line">Kestrel</span>
      <span class="brand-line brand-line--small">Picture House</span>
    </div>
    <p class="back-url">www.kestrelpicturehouse.example</p>
  </section>

</main>
</body>
</html>
```